Business Card Design

I am an Event and Wedding Planner in need of an eye catching business card featuring my logo (attached), my contact details, and my company tagline (Making every celebration glow with wonder...) I would like the tagline in font similar the logo's font.
Updates
I have just noticed that my logo has a misspelling so for the final design, I will be uploading a corrected logo as soon as I have it.
My apologies.
Reason: Waiting on a corrected logo...Lantern is misspelled and it should say Weddings not Wedding
The logo has been corrected so now Lantern is spelled correctly and it says Weddings instead of Wedding. Please use Edwardian Script ITC as the font for the tagline so it will match the logo. Thank you for your patience.
Target Market(s)
Engaged couples and people hosting milestone celebrations. 25-50 years old, predominately female
Industry/Entity Type
Business
Contact Information for Business Card
Rosalind Merrow, Event Manager / Owner, Mobile: 0491 868 254, Email: rosalind@velvetlanternco.com.au, www.velvetlanternco.com.au, Making every celebration glow with wonder...

```html
<!DOCTYPE html>
<html lang="en">
<head>
<meta charset="utf-8">
<title>Velvet Lantern – Business Card</title>
<link rel="stylesheet" href="https://fonts.googleapis.com/css2?family=Pinyon+Script&family=Montserrat:wght@700&family=Michroma&display=swap">
<style>
  :root {
    --page: #ecebe8;
    --card: #ffffff;
    --frame: #d0353d;
    --ink: #111111;
    --band: #0d0d0d;
    --soft: #e4e4e4;
    --muted: #444444;
    --rule: #bbbbbb;
  }
  * { box-sizing: border-box; margin: 0; padding: 0; }
  html, body { width: 1069px; height: 1200px; overflow: hidden; background: var(--page); }
  .canvas { position: relative; width: 1069px; height: 1200px; }
  .card {
    position: absolute; left: 104px; width: 860px; height: 490px;
    background: var(--card); border: 14px solid var(--frame);
    box-shadow: 0 6px 18px rgba(0,0,0,.18); overflow: hidden;
  }
  .card--front { top: 70px; }
  .card--back { top: 640px; }

  .brand { position: absolute; display: flex; flex-direction: column; align-items: flex-start; }
  .brand__mark { display: flex; align-items: center; gap: 12px; }
  .brand__name {
    font-family: "Montserrat", sans-serif; font-weight: 700; color: var(--ink);
    line-height: 1; white-space: nowrap;
  }
  .brand__dot { border-radius: 50%; background: var(--frame); }
  .brand__tagline {
    font-family: "Pinyon Script", cursive; color: var(--ink); white-space: nowrap;
    border-top: 1px solid var(--rule); line-height: 1.2;
  }

  .card--front .brand { left: 150px; top: 150px; }
  .card--front .brand__name { font-size: 58px; }
  .card--front .brand__dot { width: 16px; height: 16px; }
  .card--front .brand__tagline { font-size: 36px; margin-top: 16px; padding-top: 8px; }

  .front__band {
    position: absolute; left: 0; right: 0; bottom: 0; height: 64px; background: var(--band);
    display: flex; align-items: center; justify-content: flex-end; padding-right: 40px;
  }
  .front__web { font-family: "Michroma", sans-serif; font-size: 14px; letter-spacing: 3px; color: #fff; }

  .card--back .brand { left: 40px; top: 110px; }
  .card--back .brand__name { font-size: 36px; }
  .card--back .brand__dot { width: 12px; height: 12px; }
  .card--back .brand__tagline { font-size: 25px; margin-top: 12px; padding-top: 6px; }

  .contact {
    position: absolute; right: 30px; top: 24px; display: flex; gap: 16px;
    padding-left: 16px; border-left: 2px solid var(--band);
  }
  .contact__list { list-style: none; font-family: "Michroma", sans-serif; font-size: 12px; color: var(--muted); text-align: right; }
  .contact__list li { height: 30px; line-height: 30px; white-space: nowrap; }
  .contact__icons { display: flex; flex-direction: column; border-left: 2px solid var(--band); padding-left: 10px; }
  .contact__icons svg { width: 18px; height: 30px; }

  .back__band {
    position: absolute; left: 0; right: 0; top: 290px; height: 96px; background: var(--band);
    display: flex; align-items: center; justify-content: space-between; padding: 0 40px;
  }
  .person__name {
    font-family: "Montserrat", sans-serif; font-weight: 700; font-size: 34px; color: #fff;
    text-transform: uppercase; letter-spacing: 1px; white-space: nowrap;
  }
  .person__role {
    font-family: "Michroma", sans-serif; font-size: 12px; color: #fff; letter-spacing: 1.5px;
    text-transform: uppercase; white-space: nowrap;
  }
  .back__address {
    position: absolute; left: 0; right: 0; top: 398px; height: 46px; background: var(--soft);
    font-family: "Michroma", sans-serif; font-size: 13px; color: var(--muted);
    display: flex; align-items: center; padding-left: 40px; letter-spacing: 1px; white-space: nowrap;
  }
</style>
</head>
<body>
<main class="canvas">
  <section class="card card--front" aria-label="Card front">
    <div class="brand">
      <div class="brand__mark"><span class="brand__name">Velvet Lantern</span><span class="brand__dot"></span></div>
      <p class="brand__tagline">Making every celebration glow with wonder...</p>
    </div>
    <div class="front__band"><span class="front__web">www.velvetlanternco.com.au</span></div>
  </section>

  <section class="card card--back" aria-label="Card back">
    <div class="brand">
      <div class="brand__mark"><span class="brand__name">Velvet Lantern</span><span class="brand__dot"></span></div>
      <p class="brand__tagline">Making every celebration glow with wonder...</p>
    </div>
    <div class="contact">
      <ul class="contact__list">
        <li>0491 868 254</li>
        <li>0387 412 506</li>
        <li>rosalind@velvetlanternco.com.au</li>
        <li>www.velvetlanternco.com.au</li>
      </ul>
      <div class="contact__icons">
        <svg viewBox="0 0 18 30" aria-hidden="true"><rect x="5" y="7" width="8" height="15" rx="1.5" fill="none" stroke="#111" stroke-width="1.6"/><line x1="8" y1="19" x2="10" y2="19" stroke="#111" stroke-width="1.6"/></svg>
        <svg viewBox="0 0 18 30" aria-hidden="true"><path d="M4 9c0 7 5 12 10 12l1.5-3-3-1.5-1.5 1.5c-2-1-4-3-5-5l1.5-1.5L6 8.5z" fill="#111"/></svg>
        <svg viewBox="0 0 18 30" aria-hidden="true"><rect x="2" y="9" width="14" height="11" fill="none" stroke="#111" stroke-width="1.6"/><path d="M2 9l7 6 7-6" fill="none" stroke="#111" stroke-width="1.6"/></svg>
        <svg viewBox="0 0 18 30" aria-hidden="true"><circle cx="9" cy="15" r="7" fill="none" stroke="#111" stroke-width="1.6"/><path d="M2 15h14M9 8c-3 4-3 10 0 14M9 8c3 4 3 10 0 14" fill="none" stroke="#111" stroke-width="1.2"/></svg>
      </div>
    </div>
    <div class="back__band">
      <span class="person__name">Rosalind Merrow</span>
      <span class="person__role">Event Manager / Owner</span>
    </div>
    <div class="back__address">24 Harbour Lane, Level 3, Fitzroy VIC</div>
  </section>
</main>
</body>
</html>
```